Veldmark Supplies Business Card

Professional business card that stand out to our potential customers. Front and back with clean modern design

Industry/Entity Type

Oil and gas

Contact Information for Business Card

Name, address, website , office phone and cell number

Requirements
Must have
• Editable files for each employee

```html
<!DOCTYPE html>
<html lang="en">
<head>
<meta charset="utf-8">
<title>Veldmark Supplies Business Card</title>
<link rel="stylesheet" href="https://fonts.googleapis.com/css2?family=Montserrat:wght@400;500;800&display=swap">
<style>
  :root {
    --brand-red: #ec2227;
    --brand-blue: #0bafd0;
    --card-white: #ffffff;
    --ink: #1d1d1d;
    --stage: #2a2a2a;
  }
  * { margin: 0; padding: 0; box-sizing: border-box; }
  html, body { width: 1200px; height: 880px; overflow: hidden; }
  body {
    background: var(--stage);
    font-family: "Montserrat", Arial, sans-serif;
    position: relative;
  }
  .card {
    position: absolute;
    width: 540px;
    height: 309px;
    overflow: hidden;
    box-shadow: 0 14px 30px rgba(0,0,0,0.45);
  }
  .card-front { left: 120px; top: 80px; background: var(--brand-red); }
  .card-back { left: 540px; top: 470px; background: var(--card-white); }

  .front-brand {
    position: absolute;
    left: 0; right: 0; top: 0; bottom: 0;
    display: flex; align-items: center; justify-content: center; gap: 14px;
  }
  .front-brand .brand-mark { width: 34px; height: 34px; background: var(--card-white); }
  .front-brand .brand-name {
    color: var(--card-white);
    font-weight: 800;
    font-size: 30px;
    letter-spacing: 1px;
    text-transform: uppercase;
  }

  .back-art { position: absolute; inset: 0; }
  .back-brand {
    position: absolute;
    left: 30px; top: 118px; width: 200px;
    display: flex; align-items: center; gap: 10px;
  }
  .back-brand .brand-mark { width: 22px; height: 22px; background: var(--brand-red); flex: none; }
  .back-brand .brand-name {
    color: var(--brand-red);
    font-weight: 800;
    font-size: 17px;
    line-height: 1.15;
    text-transform: uppercase;
  }

  .contact {
    position: absolute;
    left: 292px; top: 26px; width: 240px;
    color: var(--ink);
  }
  .contact-name {
    color: var(--brand-red);
    font-weight: 800;
    font-size: 19px;
    letter-spacing: 0.3px;
    text-transform: uppercase;
  }
  .contact-role { font-size: 11px; margin-top: 1px; }
  .contact-address { font-size: 11px; line-height: 1.35; margin-top: 8px; }
  .contact-list { list-style: none; margin-top: 8px; font-size: 11px; }
  .contact-list li { display: flex; align-items: center; gap: 7px; height: 16px; }
  .contact-icon {
    width: 12px; height: 12px; background: var(--brand-red);
    display: flex; align-items: center; justify-content: center; flex: none;
  }
  .contact-icon svg { width: 8px; height: 8px; }
  .web-accent { color: var(--brand-red); }
</style>
</head>
<body>

<section class="card card-front" aria-label="Card front">
  <div class="front-brand">
    <span class="brand-mark"></span>
    <span class="brand-name">Veldmark Supplies</span>
  </div>
</section>

<section class="card card-back" aria-label="Card back">
  <svg class="back-art" viewBox="0 0 540 309" width="540" height="309" aria-hidden="true">
    <line x1="214" y1="98" x2="260" y2="205" stroke="#ec2227" stroke-width="1.2"/>
    <line x1="232" y1="80" x2="270" y2="168" stroke="#ec2227" stroke-width="1.2"/>
    <line x1="210" y1="70" x2="278" y2="228" stroke="#0bafd0" stroke-width="1.2"/>
    <path d="M0,262 C170,250 280,235 345,190 C300,228 180,258 0,272 Z" fill="#0bafd0"/>
    <path d="M0,280 C210,270 320,240 395,200 C455,168 495,158 540,152 L540,309 L0,309 Z" fill="#ec2227"/>
  </svg>

  <div class="back-brand">
    <span class="brand-mark"></span>
    <span class="brand-name">Veldmark<br>Supplies</span>
  </div>

  <div class="contact">
    <h1 class="contact-name">Dalen Corwick</h1>
    <p class="contact-role">President</p>
    <p class="contact-address">482 Brennan Ave, Ste 210<br>Marlow, TX 75390</p>
    <ul class="contact-list">
      <li><span class="contact-icon"><svg viewBox="0 0 8 8"><rect x="1" y="3" width="6" height="4" fill="#fff"/><rect x="0.5" y="1" width="7" height="1.5" fill="#fff"/></svg></span>555-214-3086</li>
      <li><span class="contact-icon"><svg viewBox="0 0 8 8"><rect x="2" y="0.5" width="4" height="7" rx="0.6" fill="#fff"/></svg></span>000-000-9999</li>
      <li><span class="contact-icon"><svg viewBox="0 0 8 8"><rect x="0.5" y="1.5" width="7" height="5" fill="none" stroke="#fff" stroke-width="1"/><path d="M0.5 1.5 L4 4.5 L7.5 1.5" fill="none" stroke="#fff" stroke-width="1"/></svg></span>info@example-youremail.com</li>
      <li><span class="contact-icon"><svg viewBox="0 0 8 8"><circle cx="4" cy="4" r="3.3" fill="#fff"/></svg></span>www.<span class="web-accent">example-yourwebsite</span>.com</li>
    </ul>
  </div>
</section>

</body>
</html>
```